New Webpage for High Class Expert Witness Services Company

We are looking for a minimalist design for a webpage that just has our logo and an entry form offer to connect with one of our Liaisons.
The entry form should just ask for Name, Email, Contact Info and Description of Project.

Company Name is: The Marlowe Crest Advisory Services

Number of Pages Required

1 page

```html
<!DOCTYPE html>
<html lang="en">
<head>
<meta charset="utf-8">
<title>The Marlowe Crest Advisory Services — Expert Witness Support</title>
<link href="https://fonts.googleapis.com/css2?family=Gilda+Display&family=Outfit:wght@400;500&display=swap" rel="stylesheet">
<style>
  :root {
    --night: #040b16;
    --night-soft: #0d1a2c;
    --night-glow: #1b2a3e;
    --ink: #000000;
    --paper: #ffffff;
    --text-light: #ffffff;
    --text-dark: #111111;
    --field-border: #d9d9d9;
    --ring: #8a8d92;
  }
  * { box-sizing: border-box; margin: 0; padding: 0; }
  html, body { width: 1200px; height: 782px; overflow: hidden; background: var(--night); }
  body { font-family: "Outfit", sans-serif; color: var(--text-light); }
  .page { position: relative; width: 1200px; height: 782px; overflow: hidden; background: var(--night); }

  .backdrop {
    position: absolute; left: 0; top: 100px; width: 640px; height: 560px;
    background: radial-gradient(ellipse at 60% 45%, var(--night-glow) 0%, var(--night-soft) 40%, rgba(4,11,22,0) 75%);
  }

  .brand { position: absolute; left: 65px; top: 82px; display: flex; align-items: center; gap: 10px; }
  .brand-mark { width: 14px; height: 14px; background: var(--text-light); }
  .brand-name { font-family: "Gilda Display", serif; font-size: 19px; letter-spacing: 1.5px; text-transform: uppercase; color: var(--text-light); line-height: 1.15; }

  .hero-title { position: absolute; left: 63px; top: 152px; font-family: "Gilda Display", serif; font-weight: 400; font-size: 66px; line-height: 79px; }
  .hero-rule { position: absolute; left: 63px; top: 323px; width: 68px; height: 3px; background: var(--text-light); }
  .hero-lead { position: absolute; left: 63px; top: 355px; font-size: 22px; font-weight: 400; }

  .feature { position: absolute; left: 63px; }
  .feature h3 { font-family: "Gilda Display", serif; font-weight: 400; font-size: 25px; line-height: 30px; }
  .feature p { font-size: 14.5px; line-height: 20px; margin-top: 2px; }

  .hotline { position: absolute; left: 62px; top: 642px; display: flex; align-items: center; gap: 10px; }
  .hotline-icon { width: 65px; height: 65px; border-radius: 50%; background: var(--paper); border: 6px solid var(--ring); display: flex; align-items: center; justify-content: center; }
  .hotline-label { font-size: 11px; display: block; }
  .hotline-number { font-family: "Gilda Display", serif; font-size: 26px; letter-spacing: 1px; display: block; line-height: 30px; }

  .consult-card { position: absolute; left: 612px; top: 79px; width: 525px; height: 628px; background: var(--paper); border-radius: 17px; padding: 0 33px; color: var(--text-dark); }
  .consult-title { font-family: "Gilda Display", serif; font-weight: 400; font-size: 44px; margin-top: 30px; line-height: 52px; }
  .consult-intro { font-size: 16px; line-height: 21px; margin-top: 18px; }
  .consult-form { margin-top: 33px; }
  .field { display: block; width: 458px; height: 50px; border: 1px solid var(--field-border); border-radius: 2px; padding: 0 16px; font-family: "Outfit", sans-serif; font-size: 13px; color: var(--text-dark); margin-bottom: 25px; background: var(--paper); }
  .field::placeholder, .field-message::placeholder { color: var(--text-dark); }
  .field-message { height: 117px; padding: 18px 16px; resize: none; margin-bottom: 33px; }
  .submit { width: 142px; height: 45px; background: var(--ink); color: var(--paper); border: 0; font-family: "Outfit", sans-serif; font-size: 15px; font-weight: 500; }
</style>
</head>
<body>
<main class="page">
  <div class="backdrop" role="img" aria-label="Night skyline of a city with a lit bridge over the water"></div>

  <div class="brand">
    <span class="brand-mark"></span>
    <span class="brand-name">The Marlowe Crest<br>Advisory Services</span>
  </div>

  <h1 class="hero-title">Expert Witness<br>Support</h1>
  <div class="hero-rule"></div>
  <p class="hero-lead">Trusted experts for legal and defense cases</p>

  <section class="feature" style="top:405px">
    <h3>Confidential Handling</h3>
    <p>Your information is always secure and protected.</p>
  </section>
  <section class="feature" style="top:479px">
    <h3>Fast Response</h3>
    <p>We understand time is critical. We respond quickly.</p>
  </section>
  <section class="feature" style="top:553px">
    <h3>Verified Experts</h3>
    <p>Our experts are qualified, experienced, and reliable.</p>
  </section>

  <div class="hotline">
    <span class="hotline-icon">
      <svg width="26" height="26" viewBox="0 0 24 24" fill="none" stroke="#111" stroke-width="1.4" stroke-linecap="round" stroke-linejoin="round" aria-hidden="true">
        <path d="M22 16.9v3a2 2 0 0 1-2.2 2 19.8 19.8 0 0 1-8.6-3.1 19.5 19.5 0 0 1-6-6A19.8 19.8 0 0 1 2.1 4.2 2 2 0 0 1 4.1 2h3a2 2 0 0 1 2 1.7c.1.9.4 1.8.7 2.7a2 2 0 0 1-.5 2.1L8 9.8a16 16 0 0 0 6 6l1.3-1.3a2 2 0 0 1 2.1-.4c.9.3 1.8.6 2.7.7a2 2 0 0 1 1.7 2z"/>
        <path d="M15 5a5 5 0 0 1 4 4M15 1a9 9 0 0 1 8 8"/>
      </svg>
    </span>
    <span>
      <span class="hotline-label">Need Immediate Assistance?</span>
      <span class="hotline-number">555 014 2278</span>
    </span>
  </div>

  <section class="consult-card">
    <h2 class="consult-title">Request a Consultation</h2>
    <p class="consult-intro">Fill out the form below and our team will get back to you shortly.</p>
    <form class="consult-form">
      <input class="field" type="text" placeholder="Full Name*">
      <input class="field" type="email" placeholder="Email Address*">
      <input class="field" type="tel" placeholder="Phone Number*">
      <textarea class="field field-message" placeholder="Your message......"></textarea>
      <button class="submit" type="button">Submit</button>
    </form>
  </section>
</main>
</body>
</html>
```